Business Card Design

Business Card for professional consulting firm working with large financial institutions.

Target Market(s)

Executive buyers

Industry/Entity Type

Banking

Contact Information for Business Card

Mild creativity wanted. Not boring, but do elaborate artwork.

Font styles to use
Serif
Sans Serif

Colors

Designer to choose colors to be used in the design.

Requirements
Must have
• Standard business card features - company name, individual name, telephone, website, email, locations.
Nice to have
• Two colors
Should not have
• too many colors, fancy printing, cartoons.

```html
<!DOCTYPE html>
<html lang="en">
<head>
<meta charset="utf-8">
<title>northvale — Business Card</title>
<link rel="stylesheet" href="https://fonts.googleapis.com/css2?family=Tinos:wght@400;700&display=swap">
<style>
  :root {
    --ink: #0b0b0b;
    --ink-soft: #1c1c1c;
    --paper: #ffffff;
    --paper-shade: #ececec;
    --silver: #d6d6d6;
    --silver-dim: #9a9a9a;
    --arc-grey: #c4c4c4;
    --backdrop: #e6e4e1;
  }
  * { margin: 0; padding: 0; box-sizing: border-box; }
  html, body { width: 1200px; height: 886px; overflow: hidden; }
  body {
    background: var(--backdrop);
    font-family: "Tinos", "Times New Roman", serif;
    display: flex; flex-direction: column; align-items: center; justify-content: center;
    gap: 58px;
  }
  .card {
    position: relative;
    width: 620px; height: 354px;
    border-radius: 26px;
    overflow: hidden;
    box-shadow: 0 10px 26px rgba(0,0,0,.22);
  }
  .card-front {
    background: linear-gradient(100deg, var(--ink) 0%, var(--ink-soft) 48%, #3a3a3a 58%, var(--ink) 72%);
    display: flex; align-items: center; justify-content: center;
  }
  .wordmark {
    font-family: "Tinos", "Times New Roman", serif;
    font-weight: 400;
    font-size: 52px;
    letter-spacing: 1px;
  }
  .card-front .wordmark { color: var(--silver); }
  .card-back { background: var(--paper); }
  .card-back svg.band { position: absolute; inset: 0; }
  .back-info {
    position: absolute; top: 36px; left: 34px; right: 30px;
    display: flex; align-items: flex-start;
    color: var(--silver);
  }
  .person { width: 178px; }
  .person-name { font-size: 24px; font-weight: 700; color: var(--silver); line-height: 1.05; }
  .person-title { font-size: 16px; color: var(--silver-dim); }
  .divider { width: 1px; height: 58px; background: var(--silver-dim); margin: 4px 24px 0; }
  .address, .contact { font-size: 15px; line-height: 1.28; color: var(--silver); }
  .address { width: 196px; }
  .contact { margin-left: 0; }
  .card-back .wordmark {
    position: absolute; left: 0; right: 0; top: 212px;
    text-align: center; color: var(--ink); font-size: 46px;
  }
</style>
</head>
<body>
  <section class="card card-front" aria-label="Card front">
    <span class="wordmark">northvale</span>
  </section>

  <section class="card card-back" aria-label="Card back">
    <svg class="band" width="620" height="354" viewBox="0 0 620 354" aria-hidden="true">
      <defs>
        <linearGradient id="paperShade" x1="0" y1="0" x2="0" y2="1">
          <stop offset="0" stop-color="var(--paper-shade)"/>
          <stop offset="1" stop-color="var(--paper)"/>
        </linearGradient>
      </defs>
      <rect width="620" height="354" fill="url(#paperShade)"/>
      <path d="M0 0 H620 V196 C540 120 380 104 240 116 C140 124 60 140 0 160 Z" fill="var(--ink)"/>
      <path d="M620 196 C540 120 380 104 240 116 C380 116 520 140 620 214 Z" fill="var(--arc-grey)"/>
    </svg>
    <div class="back-info">
      <div class="person">
        <p class="person-name">Daniel Reeve</p>
        <p class="person-title">Managing Director</p>
      </div>
      <span class="divider"></span>
      <div class="address">
        <p>northvale</p>
        <p>412 Harbor View Road</p>
        <p>Juneau, Alaska 99801</p>
      </div>
      <span class="divider"></span>
      <div class="contact">
        <p>555 210 4417</p>
        <p>info@northvale.com</p>
        <p>www.northvale.com</p>
      </div>
    </div>
    <span class="wordmark">northvale</span>
  </section>
</body>
</html>
```